Redesign of business card for Cedar Ridge Mechanical

We are looking for a new design for our business cards for Cedar Ridge Mechanical. We are a plumbing & HVAC construction company, operating on the West Coast of Canada and USA. Logo attached.
Industry/Entity Type
Construction - Plumbing & HVAC
Contact Information for Business Card
Name, address, phone numbers, email, website address
Look and feel
Each slider illustrates characteristics of the customer's brand and the style your logo design should communicate.

```html
<!DOCTYPE html>
<html lang="en">
<head>
<meta charset="utf-8">
<title>Cedar Ridge Mechanical – Business Card</title>
<link href="https://fonts.googleapis.com/css2?family=Montserrat:wght@400;500;600;700&display=swap" rel="stylesheet">
<style>
  :root {
    --backdrop: #e8e5e0;
    --card-light: #ffffff;
    --card-dark: #262626;
    --ink: #1c1c1c;
    --ink-soft: #2a2a2a;
    --paper: #ffffff;
  }
  * { margin: 0; padding: 0; box-sizing: border-box; }
  html, body {
    width: 900px; height: 1200px; overflow: hidden;
    background: var(--backdrop);
    font-family: "Montserrat", Arial, sans-serif;
  }
  .canvas { position: relative; width: 900px; height: 1200px; }

  .card {
    position: absolute;
    border-radius: 20px;
    overflow: hidden;
  }
  .card--front { left: 80px; top: 130px; width: 742px; height: 442px; background: var(--card-light); color: var(--ink); }
  .card--back  { left: 78px; top: 638px; width: 744px; height: 442px; background: var(--card-dark); color: var(--paper); }

  .holder { position: absolute; left: 37px; top: 48px; }
  .holder__name { font-size: 25px; font-weight: 700; line-height: 1.1; }
  .holder__title { font-size: 16px; font-weight: 500; margin-top: 4px; }

  .address { position: absolute; left: 40px; top: 258px; font-size: 16px; line-height: 21px; }

  .contacts { position: absolute; left: 38px; top: 330px; list-style: none; font-size: 16px; }
  .contacts li { display: flex; align-items: center; height: 31px; }
  .contacts svg { width: 15px; height: 15px; margin-right: 12px; fill: var(--ink-soft); }

  .brand {
    position: absolute;
    display: flex; align-items: center; gap: 18px;
    font-weight: 700; text-transform: uppercase; letter-spacing: 1px;
  }
  .brand__mark { flex: none; width: 62px; height: 62px; }
  .brand__name { font-size: 28px; line-height: 34px; }
  .card--front .brand { left: 310px; top: 175px; }
  .card--front .brand__mark { background: var(--ink); }
  .card--front .brand__name { color: var(--ink); }
  .card--back .brand { left: 210px; top: 186px; }
  .card--back .brand__mark { background: var(--paper); }
  .card--back .brand__name { color: var(--paper); }
</style>
</head>
<body>
<main class="canvas">
  <section class="card card--front" aria-label="Card front">
    <div class="holder">
      <p class="holder__name">Daniel Reyes</p>
      <p class="holder__title">Managing Director</p>
    </div>
    <address class="address" style="font-style:normal">240 Harbor View Road<br>Lakewood, WA 98499</address>
    <ul class="contacts">
      <li>
        <svg viewBox="0 0 24 24" aria-hidden="true"><path d="M6.6 10.8a15.1 15.1 0 0 0 6.6 6.6l2.2-2.2c.3-.3.7-.4 1-.2 1.1.4 2.3.6 3.6.6.6 0 1 .4 1 1V20c0 .6-.4 1-1 1A17 17 0 0 1 3 4c0-.6.4-1 1-1h3.5c.6 0 1 .4 1 1 0 1.3.2 2.5.6 3.6.1.3 0 .7-.2 1z"/></svg>
        888.555.0147
      </li>
      <li>
        <svg viewBox="0 0 24 24" aria-hidden="true"><path d="M2 5h20v3l-10 6L2 8z M2 10l10 6 10-6v9H2z"/></svg>
        info@cedarridgemechanical.com
      </li>
      <li>
        <svg viewBox="0 0 24 24" aria-hidden="true"><path d="M12 2a10 10 0 1 0 0 20 10 10 0 0 0 0-20zm-1 17.9A8 8 0 0 1 5 8l4 4v1a2 2 0 0 0 2 2zm6.9-2.5A2 2 0 0 0 16 16h-1v-3a1 1 0 0 0-1-1H8v-2h2a1 1 0 0 0 1-1V7h2a2 2 0 0 0 2-2v-.4a8 8 0 0 1 2.9 12.8z"/></svg>
        www.cedarridgemechanical.com
      </li>
    </ul>
    <div class="brand">
      <span class="brand__mark" aria-hidden="true"></span>
      <span class="brand__name">Cedar Ridge<br>Mechanical</span>
    </div>
  </section>

  <section class="card card--back" aria-label="Card back">
    <div class="brand">
      <span class="brand__mark" aria-hidden="true"></span>
      <span class="brand__name">Cedar Ridge<br>Mechanical</span>
    </div>
  </section>
</main>
</body>
</html>
```